Bramblewood Card Company Business Cards

We are a trading card store with Glimmorax, sports and other TCG cards, we need a business card design that encompasses a clean cut, modern style with a retro flare. website is bramblewoodcardco.com for reference. Can utilize a comic book era feel or a more modern outdoor feel to utilize the "Pacific Northwest" elements of tress, mountains, etc.

Industry/Entity Type

Trading cards and collectibles

Contact Information for Business Card

business name, email address, phone number, name, owner job title

Font styles to use
Sans Serif

```html
<!DOCTYPE html>
<html lang="en">
<head>
<meta charset="utf-8">
<title>Bramblewood Card Company – Business Cards</title>
<link rel="stylesheet" href="https://fonts.googleapis.com/css2?family=Montserrat:wght@400;500;600;800&display=swap">
<style>
  :root {
    --backdrop: #e4e2e3;
    --card: #ffffff;
    --brand-cyan: #1ab8dc;
    --brand-grey: #6f6f70;
    --ink: #1d1d1d;
  }
  * { margin: 0; padding: 0; box-sizing: border-box; }
  html, body {
    width: 1200px; height: 1108px; overflow: hidden;
    background: var(--backdrop);
    font-family: "Montserrat", sans-serif;
    color: var(--ink);
  }
  .card {
    position: absolute;
    left: 228px;
    width: 756px;
    background: var(--card);
  }
  .card--front { top: 56px; height: 462px; }
  .card--back  { top: 575px; height: 444px; }

  .front-brand {
    position: absolute;
    left: 140px; top: 208px;
    width: 185px;
    display: flex; flex-direction: column; align-items: center; gap: 10px;
    text-align: center;
  }
  .brand-square {
    width: 34px; height: 34px;
    background: var(--brand-grey);
  }
  .brand-name {
    font-weight: 800;
    color: var(--brand-grey);
    text-transform: uppercase;
    line-height: 1.15;
  }
  .front-brand .brand-name { font-size: 17px; }

  .divider {
    position: absolute;
    left: 348px; top: 170px;
    width: 2px; height: 148px;
    background: var(--brand-cyan);
  }
  .contact {
    position: absolute;
    left: 365px; top: 166px;
  }
  .contact__name {
    font-size: 30px; font-weight: 600;
    color: var(--brand-cyan);
    line-height: 1.1;
  }
  .contact__role {
    font-size: 17px; font-weight: 400;
    margin-top: 2px;
  }
  .contact__list { list-style: none; margin-top: 14px; }
  .contact__item {
    display: flex; align-items: center;
    font-size: 17.5px; font-weight: 400;
    height: 30px;
  }
  .contact__item svg { width: 18px; height: 18px; margin-right: 10px; flex: none; fill: var(--brand-cyan); }
  .contact__item:first-child svg { margin-right: 8px; }

  .address {
    position: absolute;
    left: 0; right: 0; top: 410px;
    text-align: center;
    font-size: 17px; font-weight: 400;
  }

  .back-brand {
    position: absolute;
    left: 0; right: 0; top: 150px;
    display: flex; flex-direction: column; align-items: center; gap: 22px;
    text-align: center;
  }
  .back-brand .brand-square { width: 60px; height: 60px; }
  .back-brand .brand-name { font-size: 36px; }
</style>
</head>
<body>

<section class="card card--front">
  <div class="front-brand">
    <span class="brand-square"></span>
    <span class="brand-name">Bramblewood Card Company</span>
  </div>

  <span class="divider"></span>

  <div class="contact">
    <h1 class="contact__name">Daniel Harper</h1>
    <p class="contact__role">Owner</p>
    <ul class="contact__list">
      <li class="contact__item">
        <svg viewBox="0 0 24 24" aria-hidden="true"><path d="M6.6 10.8a15.1 15.1 0 0 0 6.6 6.6l2.2-2.2a1 1 0 0 1 1-.25 11.4 11.4 0 0 0 3.6.57 1 1 0 0 1 1 1V20a1 1 0 0 1-1 1A17 17 0 0 1 3 4a1 1 0 0 1 1-1h3.5a1 1 0 0 1 1 1c0 1.25.2 2.45.57 3.57a1 1 0 0 1-.25 1z"/></svg>
        06-98765432
      </li>
      <li class="contact__item">
        <svg viewBox="0 0 24 24" aria-hidden="true"><path d="M2 5h20v2l-10 6L2 7z"/><path d="M2 9l10 6 10-6v10H2z"/></svg>
        info@bramblewoodcardcompany.com
      </li>
      <li class="contact__item">
        <svg viewBox="0 0 24 24" aria-hidden="true"><path d="M12 2a10 10 0 1 0 0 20 10 10 0 0 0 0-20zm6.9 6h-3a15.6 15.6 0 0 0-1.3-4A8 8 0 0 1 18.9 8zM12 4c.8 1.2 1.5 2.5 1.9 4h-3.8c.4-1.5 1.1-2.8 1.9-4zM4.3 14a8 8 0 0 1 0-4h3.4a16 16 0 0 0 0 4zm.8 2h3a15.6 15.6 0 0 0 1.3 4A8 8 0 0 1 5.1 16zm3-8h-3a8 8 0 0 1 4.3-4 15.6 15.6 0 0 0-1.3 4zM12 20c-.8-1.2-1.5-2.5-1.9-4h3.8c-.4 1.5-1.1 2.8-1.9 4zm2.3-6H9.7a14.6 14.6 0 0 1 0-4h4.6a14.6 14.6 0 0 1 0 4zm.3 6a15.6 15.6 0 0 0 1.3-4h3a8 8 0 0 1-4.3 4zm1.7-6a16 16 0 0 0 0-4h3.4a8 8 0 0 1 0 4z"/></svg>
        www.bramblewoodcardcompany.com
      </li>
    </ul>
  </div>

  <p class="address">4820 Cedar Ridge Ave Suite210 Tacoma, Washington 98402</p>
</section>

<section class="card card--back">
  <div class="back-brand">
    <span class="brand-square"></span>
    <span class="brand-name">Bramblewood<br>Card Company</span>
  </div>
</section>

</body>
</html>
```